High-end law practice specializing in closely held business succession planning and complex estates

Solo practitioner whose practice specializes in high-net worth, complex estate planning needs muliple versions of letterhead black and white, please. Letterhead should incorporate slogan, "Protecting your family business is my business," for one and "Complex Estate Planning"; third with no slogan. All for The Law Office of Marcy Lynn Pettibone, PC, 418 Cedar Hollow Ln., Newport News, Virginia 23648, Tel. 757-555-0142 Fax tbd email: marcy@mlplawgroup.example; Marcy Lynn Pettibone, Esq., principal, licensed in VA, NY, DC
Updates

Project Deadline Extended
Reason: My internet service went down and I can only view designs on my smart phone -- it's just too hard to review. So sorry! Working with my ISP now. Please be patient!

Target Market(s)

High net worth clients with complex estate planning needs, family businesses, family farmers, family foresters -- people with unique estate/succession planning needs who need a specialist who understands them.

Industry/Entity Type

Business

Font styles to use
Script

Requirements
Must have
• A high-end look and feel, connoting trustworthiness, special knowledge, and expertise.

```html
<!DOCTYPE html>
<html lang="en">
<head>
<meta charset="utf-8">
<title>Letterhead – The Law Office of Marcy Lynn Pettibone, PC</title>
<link href="https://fonts.googleapis.com/css2?family=Tinos:ital,wght@0,400;0,700;1,400&family=PT+Sans:ital@0;1&display=swap" rel="stylesheet">
<style>
  :root {
    --backdrop: #e9e7e4;
    --paper: #ffffff;
    --ink: #111111;
    --rule: #9a9a9a;
    --divider: #b5b5b5;
    --band: #000000;
    --band-edge: #6e6e6e;
    --band-text: #ffffff;
  }
  html, body {
    margin: 0;
    padding: 0;
    width: 953px;
    height: 1200px;
    overflow: hidden;
    background: var(--backdrop);
  }
  .letterhead {
    position: absolute;
    left: 159px;
    top: 157px;
    width: 634px;
    height: 896px;
    background: var(--paper);
    color: var(--ink);
    box-shadow: 0 2px 8px rgba(0,0,0,0.12);
    overflow: hidden;
  }
  .masthead {
    position: absolute;
    left: 29px;
    top: 20px;
    right: 22px;
    display: flex;
    align-items: flex-end;
    white-space: nowrap;
  }
  .firm {
    flex: 0 0 auto;
    margin-right: 8px;
  }
  .firm-name {
    margin: 0;
    font-family: "Tinos", "Times New Roman", serif;
    font-weight: 700;
    font-size: 18px;
    line-height: 23px;
    letter-spacing: -0.2px;
  }
  .firm-focus {
    margin: 4px 0 0;
    font-family: "Tinos", "Times New Roman", serif;
    font-style: italic;
    font-size: 17px;
    letter-spacing: 3.2px;
  }
  .contact {
    flex: 0 0 auto;
    border-left: 1px solid var(--divider);
    padding: 0 6px 0 7px;
    margin-bottom: 3px;
    font-family: "PT Sans", "Myriad Pro", sans-serif;
    font-size: 10px;
    line-height: 14px;
    letter-spacing: -0.1px;
  }
  .contact-address { padding-top: 7px; padding-bottom: 1px; padding-right: 0; }
  .masthead-rule {
    position: absolute;
    left: 29px;
    right: 30px;
    top: 111px;
    height: 0;
    border-top: 1px solid var(--rule);
  }
  .slogan {
    position: absolute;
    left: 0;
    right: 0;
    top: 836px;
    margin: 0;
    text-align: center;
    font-family: "PT Sans", "Myriad Pro", sans-serif;
    font-style: italic;
    font-size: 11px;
  }
  .credential-band {
    position: absolute;
    left: 0;
    right: 0;
    top: 856px;
    height: 33px;
    border-top: 3px solid var(--band-edge);
    background: var(--band);
    color: var(--band-text);
    font-family: "PT Sans", "Myriad Pro", sans-serif;
    font-size: 13px;
    line-height: 30px;
    text-align: center;
    letter-spacing: 0.2px;
    box-sizing: border-box;
  }
</style>
</head>
<body>
  <main class="letterhead">
    <header class="masthead">
      <div class="firm">
        <h1 class="firm-name">THE LAW OFFICE<br>OF MARCY LYNN PETTIBONE, PC</h1>
        <p class="firm-focus">Complex Estate Planning</p>
      </div>
      <div class="contact contact-lines">
        757-555-0142<br>
        757-555-0178<br>
        marcy@mlplawgroup.example
      </div>
      <div class="contact contact-address">
        418 Cedar Hollow Ln.,<br>
        Newport News, Virginia 23648
      </div>
    </header>
    <div class="masthead-rule"></div>

    <p class="slogan">Protecting Your Family Business is my Business</p>
    <footer class="credential-band">MARCY LYNN PETTIBONE, ESQ., PRINCIPAL, LICENSED IN VA, NY, DC</footer>
  </main>
</body>
</html>
```